female esthetician looking for an impact business card

I an an expert in skin care industry with high experience in NYC.I want my business card to look professional , an impact at first look. I do want a combination between white and gold . I believe the font will be great if is gold.. The Fonts are also important. MIRABELA COSTINA (SKIN CARE BOUTIQUE)

THIS SHOULD BE THE BUSINESS NAME, and should be placed on th eback of the card.
IN front m, the name MIRABELA COSTINA - ESTHETCIAN

BY APPOINTMENTS ONLY: 518.240.7136

Target Market(s)

HIGH END CLIENTELE

Contact Information for Business Card

iT WILL BE on a luxury paper. I neeed the wow feeling

Requirements
Should not have
• pictures

```html
<!DOCTYPE html>
<html lang="en">
<head>
<meta charset="utf-8">
<title>Mirabela Costina – Business Card</title>
<link rel="stylesheet" href="https://fonts.googleapis.com/css2?family=Lato:wght@400;700&display=swap">
<style>
  :root {
    --backdrop: #575757;
    --card: #1b1b1b;
    --gold: #e9bd22;
    --ink-light: #e6e6e6;
    --ink-muted: #c9c2a8;
  }
  * { margin: 0; padding: 0; box-sizing: border-box; }
  html, body { width: 1200px; height: 900px; overflow: hidden; }
  body {
    position: relative;
    background: var(--backdrop);
    font-family: "Lato", Arial, sans-serif;
  }
  .card {
    position: absolute;
    top: 200px;
    width: 312px;
    height: 503px;
    background: var(--card);
    box-shadow: 3px 3px 6px rgba(0, 0, 0, 0.35);
  }
  .card--front { left: 253px; border-radius: 62px 0 62px 0; }
  .card--back  { left: 627px; border-radius: 0 62px 0 62px; }

  .brand-dot {
    position: absolute;
    border-radius: 50%;
    background: var(--gold);
  }
  .card--front .brand-dot { left: 103px; top: 84px; width: 106px; height: 106px; }
  .card--front .brand-name {
    position: absolute;
    left: 0; right: 0; top: 208px;
    text-align: center;
    color: var(--gold);
    font-weight: 700;
    font-size: 14px;
    letter-spacing: 3px;
  }

  .contact { position: absolute; left: 35px; top: 326px; color: var(--ink-light); }
  .contact__name { color: var(--gold); font-weight: 700; font-size: 18px; line-height: 22px; }
  .contact__role { font-size: 14px; line-height: 16px; margin-bottom: 8px; }
  .contact__list { list-style: none; font-size: 14px; line-height: 18.5px; margin-left: -3px; }
  .contact__list li { display: flex; align-items: center; gap: 6px; }
  .contact__list svg { width: 12px; height: 12px; fill: var(--gold); flex: none; }
  .contact__address { font-size: 14px; line-height: 18px; margin: 7px 0 0 -3px; }

  .card--back .brand-dot { left: 122px; top: 182px; width: 66px; height: 66px; }
  .card--back .brand-name {
    position: absolute;
    left: 0; right: 0; top: 288px;
    text-align: center;
    color: var(--gold);
    font-weight: 400;
    font-size: 24px;
    letter-spacing: 2px;
  }
  .tagline {
    position: absolute;
    left: 0; right: 0; top: 318px;
    text-align: center;
    color: var(--ink-muted);
    font-size: 11px;
    letter-spacing: 5px;
  }
</style>
</head>
<body>
  <section class="card card--front">
    <div class="brand-dot" aria-hidden="true"></div>
    <p class="brand-name">MIRABELA COSTINA</p>
    <div class="contact">
      <p class="contact__name">MIRABELA COSTINA</p>
      <p class="contact__role">Esthetician</p>
      <ul class="contact__list">
        <li><svg viewBox="0 0 12 12"><path d="M1 4c0-2 2-3 5-3s5 1 5 3l-2 1-1-1V3H4v1L3 5 1 4zm2 2h6l1 5H2l1-5zm3 1.3a1.6 1.6 0 1 0 0 3.2 1.6 1.6 0 0 0 0-3.2z"/></svg>518.240.7136</li>
        <li><svg viewBox="0 0 12 12"><path d="M1 2.5h10v7H1zM1.5 3l4.5 3.5L10.5 3" stroke="#1b1b1b" stroke-width="0.8"/></svg>hello@mirabelacostina.com</li>
        <li><svg viewBox="0 0 12 12"><circle cx="6" cy="6" r="5"/><path d="M3 4l2 1 0 2 1 1M8 3l-1 2 2 1" stroke="#1b1b1b" stroke-width="0.9" fill="none"/></svg>www.mirabelacostina.com</li>
      </ul>
      <p class="contact__address">12345, Address Goes Here<br>Country Name, 123456</p>
    </div>
  </section>

  <section class="card card--back">
    <div class="brand-dot" aria-hidden="true"></div>
    <p class="brand-name">MIRABELA COSTINA</p>
    <p class="tagline">SKIN CARE BOUTIQUE</p>
  </section>
</body>
</html>
```